Dental Practice Billboard Design

We are a newer dental practice in need of a simple but appealing billboard for our growing dental practice to attract new patients. The practice is owned by husband and wife dentists and is family friendly in a small town in Kentucky. We try to be very friendly and caring to our patients. Would prefer a blue background for the billboard and our tooth logo to be prominent. We are partial to the Patua One font used in the image below but please feel free to tweak it as you deem necessary. The shape of the uppercase D and lowercase g are why we like that font, so fonts with a similarly shaped “D” and “g” would work as well. Please include our phone number (555) 847-1390. Please see our website Harlowbrookdentistry.example for more info on the practice if needed. Thank you! Looking forward to seeing your creation.
Updates

The dimensions will be 12ft x 24ft (3.6576m x 7.3152m). Apologies for not including this in the original prompt. Thank you all for your submissions.

Industry/Entity Type

Dental

Font styles to use
Other font styles liked:
• Patua One

Colors
0054AA
0677BA
7BADD7
CADEEF
E8F1F8
0094D4
00A9DD
6FCCEA
C7EBF8
E9F6FB
00AB8E
00BBA5
67D7C9
C6EFE9
E9F9F6
59FF00
82FF00
B8FF75
E3FFCB
F4FFEA

Requirements
Must have
• Phone number, website, Logo, Practice name “Harlow Brook Dentistry”
Should not have
• A tagline or slogan

```html
<!DOCTYPE html>
<html lang="en">
<head>
<meta charset="utf-8">
<title>Harlow Brook Dentistry Billboard</title>
<link href="https://fonts.googleapis.com/css2?family=Bitter:wght@700&display=swap" rel="stylesheet">
<style>
  :root {
    --page-bg: #808080;
    --brand-blue: #0057bc;
    --brand-green: #14b41a;
    --photo-light: #dfe9e3;
    --photo-mid: #b9c7c0;
    --photo-dark: #6f6259;
    --white: #ffffff;
  }
  * { margin: 0; padding: 0; box-sizing: border-box; }
  html, body {
    width: 1200px; height: 1059px; overflow: hidden;
    background: var(--page-bg);
    font-family: "Bitter", Georgia, serif;
  }
  .billboard {
    position: absolute; left: 50px; top: 254px;
    width: 1100px; height: 550px;
    background: var(--brand-blue);
    overflow: hidden;
    box-shadow: 0 6px 12px rgba(0,0,0,.35);
  }
  .billboard-shapes { position: absolute; inset: 0; }
  .brand {
    position: absolute; left: 548px; top: 58px;
    display: flex; align-items: center; gap: 22px;
    color: var(--white); font-weight: 700;
  }
  .brand-dot {
    width: 92px; height: 92px; border-radius: 50%;
    background: var(--white); flex: none;
  }
  .brand-name { line-height: 1; }
  .brand-name .line-main { display: block; font-size: 66px; }
  .brand-name .line-sub { display: block; font-size: 44px; margin-top: 8px; }
  .contact {
    position: absolute; right: 52px; color: var(--white); font-weight: 700;
    display: flex; align-items: center; gap: 14px;
  }
  .contact-phone { top: 298px; font-size: 60px; }
  .contact-web { top: 390px; font-size: 28px; letter-spacing: 2px; }
  .contact svg { flex: none; }
  .hours-band {
    position: absolute; left: 0; right: 0; bottom: 0; height: 76px;
    display: flex; align-items: center; justify-content: flex-end;
    padding-right: 46px; gap: 18px;
  }
  .hours-list {
    color: var(--white); font-size: 20px; letter-spacing: 1.2px;
    text-align: right; line-height: 1.32;
  }
  .hours-divider { width: 2px; height: 44px; background: var(--brand-blue); }
  .hours-title {
    color: var(--brand-blue); font-size: 23px; letter-spacing: 1.5px;
  }
</style>
</head>
<body>
  <main class="billboard">
    <svg class="billboard-shapes" width="1100" height="550" viewBox="0 0 1100 550">
      <defs>
        <linearGradient id="photoTone" x1="0" y1="0" x2="1" y2="1">
          <stop offset="0" stop-color="var(--photo-light)"/>
          <stop offset="0.6" stop-color="var(--photo-mid)"/>
          <stop offset="1" stop-color="var(--photo-dark)"/>
        </linearGradient>
      </defs>
      <rect class="hours-band-fill" x="0" y="474" width="1100" height="76" fill="var(--brand-green)"/>
      <path class="arc-frame" d="M0 0 H360 C470 40 535 150 530 290 C522 410 430 510 270 550 H0 Z" fill="var(--brand-green)"/>
      <path class="photo-area" role="img" aria-label="Photo of a dentist in a white coat and loupes scanning a patient's teeth in a bright treatment room"
            d="M0 0 H236 C380 40 505 150 500 290 C494 400 420 500 255 550 H0 Z" fill="url(#photoTone)"/>
    </svg>

    <div class="brand">
      <span class="brand-dot"></span>
      <span class="brand-name">
        <span class="line-main">Harlow Brook</span>
        <span class="line-sub">Dentistry</span>
      </span>
    </div>

    <div class="contact contact-phone">
      <span>(555) 847-1390</span>
      <svg width="42" height="42" viewBox="0 0 24 24" aria-hidden="true">
        <path fill="var(--brand-green)" d="M6.6 10.8a15.1 15.1 0 0 0 6.6 6.6l2.2-2.2a1 1 0 0 1 1-.25 11.4 11.4 0 0 0 3.6.57 1 1 0 0 1 1 1V20a1 1 0 0 1-1 1A17 17 0 0 1 3 4a1 1 0 0 1 1-1h3.5a1 1 0 0 1 1 1c0 1.25.2 2.45.57 3.57a1 1 0 0 1-.25 1z"/>
      </svg>
    </div>

    <div class="contact contact-web">
      <span>Harlowbrookdentistry.example</span>
      <svg width="38" height="38" viewBox="0 0 24 24" aria-hidden="true" fill="none" stroke="var(--brand-green)" stroke-width="2">
        <circle cx="12" cy="12" r="10"/>
        <ellipse cx="12" cy="12" rx="4.5" ry="10"/>
        <path d="M2 12h20M4 7h16M4 17h16"/>
      </svg>
    </div>

    <footer class="hours-band">
      <div class="hours-list">
        <div>Mon - Tue - Thu - Fri : 8AM - 5PM</div>
        <div>Sat - Sun - Wed : CLOSED</div>
      </div>
      <span class="hours-divider"></span>
      <div class="hours-title">OFFICE HOURS</div>
    </footer>
  </main>
</body>
</html>
```